BOLD & MINIMALIST DESIGN NEEDED

We want a very bold but minimalistic business card design that is impactful and utilizes both sides of the business card. Our current logo is included for your use.

We want bold fonts and good use of negative space. We don't want the logo to overpower the design.

Target Market(s)

Professionals who are building new commercial buildings.

Industry/Entity Type

Construction

Contact Information for Business Card

Name, Title, email, office phone, cell phone, website

Font styles to use
Serif
Sans Serif

Requirements
Must have
• Bold design!

```html
<!DOCTYPE html>
<html lang="en">
<head>
<meta charset="utf-8">
<title>Ridgeline – Business Card</title>
<link rel="stylesheet" href="https://fonts.googleapis.com/css2?family=Figtree:wght@400;500;800&display=swap">
<style>
  :root {
    --green: #8cc63f;
    --green-light: #d6e9bb;
    --ink: #111111;
    --paper: #ffffff;
    --backdrop: #262626;
  }
  * { margin: 0; padding: 0; box-sizing: border-box; }
  html, body { width: 1200px; height: 1200px; overflow: hidden; }
  body {
    background: var(--backdrop);
    font-family: "Figtree", Arial, sans-serif;
    position: relative;
  }
  .card {
    position: absolute;
    left: 188px;
    width: 825px;
    height: 481px;
    overflow: hidden;
  }
  .card--front { top: 76px; background: var(--paper); }
  .card--back {
    top: 600px;
    background: linear-gradient(90deg, var(--green-light) 0%, #a8d267 22%, #98cc53 45%, var(--green) 100%);
  }

  .brand {
    position: absolute;
    display: flex;
    align-items: center;
    gap: 12px;
    font-weight: 800;
    letter-spacing: 1px;
  }
  .brand__mark { display: block; }
  .card--front .brand { left: 60px; top: 220px; font-size: 46px; color: var(--ink); }
  .card--front .brand__mark { width: 30px; height: 30px; background: var(--green); }
  .card--back .brand {
    left: 0; right: 0; top: 195px; justify-content: center;
    font-size: 84px; color: var(--paper); gap: 20px;
  }
  .card--back .brand__mark { width: 54px; height: 54px; background: var(--paper); }

  .divider {
    position: absolute;
    left: 418px; top: 140px;
    width: 2px; height: 200px;
    background: var(--green);
  }
  .person { position: absolute; left: 453px; top: 136px; }
  .person__name {
    font-size: 33px; font-weight: 800; color: var(--green);
    line-height: 1; letter-spacing: 0.3px;
  }
  .person__title {
    margin-top: 10px; font-size: 20px; font-weight: 500; color: var(--ink);
  }
  .contacts { position: absolute; left: 453px; top: 212px; list-style: none; }
  .contacts li {
    display: flex; align-items: center; height: 34px;
    font-size: 20px; font-weight: 500; color: var(--ink);
  }
  .contacts svg { width: 20px; height: 20px; margin-right: 14px; flex: none; }

  .address {
    position: absolute; left: 39px; top: 425px;
    font-size: 20px; font-weight: 500; color: var(--ink);
  }
  .accent { position: absolute; left: 508px; top: 430px; }
</style>
</head>
<body>
  <section class="card card--front">
    <div class="brand"><span class="brand__mark"></span>RIDGELINE</div>
    <div class="divider"></div>
    <div class="person">
      <p class="person__name">MARCUS TELLEN</p>
      <p class="person__title">Managing Director</p>
    </div>
    <ul class="contacts">
      <li>
        <svg viewBox="0 0 20 20"><path d="M4 2 L8 2 L9 6 L7 8 Q9 12 12 13 L14 11 L18 12 L18 16 Q17 18 15 18 Q4 16 2 5 Q2 3 4 2Z" fill="none" stroke="var(--green)" stroke-width="1.8"/></svg>
        555-214-7730
      </li>
      <li>
        <svg viewBox="0 0 20 20"><path d="M1 7 Q10 1 19 7 L17 9 L14 7 L6 7 L3 9Z" fill="var(--green)"/><rect x="4" y="9" width="12" height="9" rx="1.5" fill="var(--green)"/></svg>
        555 000 0000
      </li>
      <li>
        <svg viewBox="0 0 20 20"><rect x="1" y="4" width="18" height="12" fill="var(--green)"/><path d="M1 4 L10 11 L19 4" fill="none" stroke="#fff" stroke-width="1.5"/></svg>
        info@yourmail.com
      </li>
      <li>
        <svg viewBox="0 0 20 20"><circle cx="10" cy="10" r="9" fill="var(--green)"/><path d="M6 5 Q9 7 8 10 Q11 12 9 16 M13 4 Q12 7 15 9" fill="none" stroke="#fff" stroke-width="1.3"/></svg>
        www.yourwebsite.com
      </li>
    </ul>
    <p class="address">482 Summit Ave, Ste 100, Austin, TX 78701</p>
    <svg class="accent" width="317" height="16" viewBox="0 0 317 16">
      <defs>
        <linearGradient id="bandFade" x1="0" x2="1">
          <stop offset="0" stop-color="#e3f0cf"/>
          <stop offset="0.5" stop-color="#8cc63f"/>
          <stop offset="1" stop-color="#8cc63f"/>
        </linearGradient>
      </defs>
      <polygon points="6,0 22,0 16,14 0,14" fill="var(--green)"/>
      <polygon points="28,0 48,0 42,14 22,14" fill="var(--ink)"/>
      <polygon points="51,0 317,0 317,14 46,14" fill="url(#bandFade)"/>
    </svg>
  </section>

  <section class="card card--back">
    <div class="brand"><span class="brand__mark"></span>RIDGELINE</div>
  </section>
</body>
</html>
```